Salon and Spa Distributor Business Card

Need a business card. We are are distributor in the salon and spa industry. We identify with natural beauty. Need a card with:
Company Name: Petal Quarry"
Title: "President & CEO"
Address
Company Phone number
email
website
Tag Line:" The Professional Salon Source"

Industry/Entity Type

Business

Contact Information for Business Card

Name: Dov Strommen
Title: "President & CEO"
Address: 31 Harlow Ln, Bexmoor, NJ 07813
Company Phone number: 800-463-5918
email: dovstrommen@petalquarry.example
website: www.petalquarry.example

Requirements
Should not have
• No black backgrounds

```html
<!DOCTYPE html>
<html lang="en">
<head>
<meta charset="utf-8">
<title>Petal Quarry – Business Card</title>
<link rel="stylesheet" href="https://fonts.googleapis.com/css2?family=Didact+Gothic&display=swap">
<style>
  :root {
    --page-bg: #ece6de;
    --card-frost: #eef0ee;
    --card-frost-edge: #dfe3e0;
    --green-deep: #1f8a3a;
    --green-mid: #2ea043;
    --green-light: #4fbf4a;
    --band-green: #49b545;
    --text-light: #e9f3e6;
    --text-soft: #cfe6c9;
    --tagline-text: #b9e4ad;
  }
  * { margin: 0; padding: 0; box-sizing: border-box; }
  html, body {
    width: 1200px;
    height: 1010px;
    overflow: hidden;
    background: var(--page-bg);
    font-family: "Didact Gothic", "Century Gothic", sans-serif;
  }
  .business-card {
    position: absolute;
    left: 110px;
    top: 220px;
    width: 980px;
    height: 570px;
    border-radius: 4px;
    overflow: hidden;
    box-shadow: 0 18px 40px rgba(60, 50, 40, 0.22);
    background: linear-gradient(160deg, var(--card-frost) 0%, var(--card-frost-edge) 100%);
  }
  .card-shapes {
    position: absolute;
    inset: 0;
  }
  .identity {
    position: absolute;
    left: 42px;
    top: 40px;
    color: var(--text-light);
  }
  .company-name {
    font-size: 46px;
    font-weight: 400;
    letter-spacing: 0.5px;
    line-height: 1.1;
  }
  .job-title {
    font-size: 20px;
    color: var(--text-soft);
    margin-top: 4px;
  }
  .contact-list {
    position: absolute;
    left: 42px;
    top: 318px;
    list-style: none;
    color: var(--text-soft);
    font-size: 23px;
  }
  .contact-list li {
    display: flex;
    align-items: center;
    height: 35px;
  }
  .contact-icon {
    width: 22px;
    height: 22px;
    margin-right: 20px;
    flex: none;
  }
  .contact-address {
    margin-top: 4px;
  }
  .tagline {
    position: absolute;
    left: 42px;
    top: 482px;
    font-size: 23px;
    color: var(--tagline-text);
  }
  .brand-mark {
    position: absolute;
    left: 700px;
    top: 262px;
    display: flex;
    align-items: center;
    gap: 14px;
    color: var(--green-mid);
    font-size: 34px;
  }
  .brand-dot {
    width: 22px;
    height: 22px;
    border-radius: 50%;
    background: var(--green-light);
    flex: none;
  }
</style>
</head>
<body>
  <div class="business-card">
    <svg class="card-shapes" width="980" height="570" viewBox="0 0 980 570" aria-hidden="true">
      <defs>
        <linearGradient id="greenPanel" x1="0" y1="0" x2="1" y2="1">
          <stop offset="0" stop-color="#2c9a3e"/>
          <stop offset="0.55" stop-color="#1f8a3a"/>
          <stop offset="1" stop-color="#27933d"/>
        </linearGradient>
      </defs>
      <path d="M0 0 H690 C600 120 530 300 660 570 H0 Z" fill="url(#greenPanel)"/>
      <path d="M702 0 C626 130 565 300 640 570" fill="none" stroke="var(--green-light)" stroke-width="6"/>
      <path d="M0 476 H616 C612 491 611 505 613 524 H0 Z" fill="var(--band-green)" opacity="0.55"/>
    </svg>

    <div class="identity">
      <h1 class="company-name">Petal Quarry</h1>
      <p class="job-title">President &amp; CEO</p>
    </div>

    <ul class="contact-list">
      <li>
        <svg class="contact-icon" viewBox="0 0 24 24" aria-hidden="true">
          <path d="M3 8 C3 5 6 4 12 4 C18 4 21 5 21 8 V10 H16 V8 H8 V10 H3 Z M6 12 H18 L20 20 H4 Z" fill="currentColor"/>
        </svg>
        800-463-5918
      </li>
      <li>
        <svg class="contact-icon" viewBox="0 0 24 24" aria-hidden="true">
          <rect x="2" y="5" width="20" height="14" fill="currentColor"/>
          <path d="M2 5 L12 13 L22 5" fill="none" stroke="#1f8a3a" stroke-width="1.6"/>
        </svg>
        dovstrommen@petalquarry.example
      </li>
      <li>
        <svg class="contact-icon" viewBox="0 0 24 24" aria-hidden="true">
          <circle cx="12" cy="12" r="9" fill="currentColor"/>
          <path d="M3 12 H21 M12 3 C8 7 8 17 12 21 M12 3 C16 7 16 17 12 21" fill="none" stroke="#1f8a3a" stroke-width="1.3"/>
        </svg>
        www.petalquarry.example
      </li>
      <li class="contact-address">31 Harlow Ln, Bexmoor, NJ 07813</li>
    </ul>

    <p class="tagline">The Professional Salon Source</p>

    <div class="brand-mark">
      <span class="brand-dot"></span>
      <span class="brand-name">Petal Quarry</span>
    </div>
  </div>
</body>
</html>
```